Packaging and labelling for Swiss made Organic CBD Oil

Visit our website www.clearleafmerida.example
We have not put any product on yet as require packaging and label design .
Website will give you a great feel for the company and how we have used
the logo . The Vextora cbd product shown is a company similar to ourselves with similar core values , we liked the clean packaging design they have .

Im happy if you want use the mandala symbol in our logo separate from
KELVORA, to separate and use the mandala symbol as a larger icon than
it appears in our logo
Clean , Pure , organic feel. Like the product to look pharmaceutical and life changing not gimmicky.
Colours to go with or be the same as our logo colours
But not too cold and clinical
Bottle size 84mm x 25mm
Label size 75mm x 30mm
Box 30mm x 30mm x 100mm
6 products
Full Spectrum :
500mg CBD (5%)
1000mg CBD ( 10% )
1500mg CBD (15%)
2000mg CBD ( 20% )
Broad spectrum THC Free
500mg CBD (5%)
Pets
500mg Broad Spectrum THC Free
Updates

Would like the design to be more modern than traditional

LABEL Information Front of Bottle - Logo KELVORA & Mandala - Mandala can be used separately as design symbol Organic Cannabis Oil 1500mg CBD (15%) Ful Spectrum 10ml Back of bottle Ingredients: Organic Cannabis Oil Extract Organic Sunflower Seed Oil THC - 0.2% Certified Swiss Organic Cultivation Shake well before use. Store in a cool , dry place and out of the each of children BOX information Front and rear Logo - KELVORA & Mandala - Mandala can be used separately as a design symbol Organic Cannabis Oil 1500mg CBD (15%) Full Spectrum Sides x 2 This product is a food supplement and is not intended to diagnose, treat, cure or prevent any disease If you are pregnant, lactating or taking any medication consult your health care practitioner Suitable for vegetarians and vegans Ingredients Organic Cannabis Oil extract Organis Sunflower Oil Store in a cool ,dry place, out of the reach of children Recommended Use 1-5 drops ( 1 drop = 7.5mg CBD ) Subject to body weight and personal requirement - visit www.clearleafmerida for more information 100% Natural 100% Organic GMO free 100% Vegan ( symbol with each ) Expiry date see bottle label Cultivated and manufactured in Switzerland

Target Market(s)

age 40 - 80

Font styles to use
Other font styles liked:
• In our website we have used Open Sans for the copy and Lato for headings .

Requirements
Must have
• look like an Industry leader
Kelvora will change the quality of peoples lives and in some cases may
even save lives so want look powerful and credible
Our Mission is - Through Delivering Pure , Premium , Organic products we will educate, inform and help people achieve healthier , happier lifestyles
Nice to have
• Colours to look good with our logo colours or be the same as our logo
colours
Logo Font - Avenir Black and Avenir Book

Font used in website - Content - Open Sans / Headings - Lato
If you have another font for the packaging information that will go well with
our logo, I'm happy for you to use your skills

```html
<!DOCTYPE html>
<html lang="en">
<head>
<meta charset="utf-8">
<title>Kelvora Organic Cannabis Oil – Label and Box Panels</title>
<link rel="stylesheet" href="https://fonts.googleapis.com/css2?family=Mulish:wght@400;800&display=swap">
<style>
  :root {
    --page-bg: #f1f2f2;
    --ink: #4b5658;
    --teal-light: #ffffff;
    --teal-mid: #d6eeee;
    --teal-deep: #8fd4d4;
    --side-top: #f3f4f4;
    --side-bottom: #79afad;
    --accent: #7fcfcf;
    --motif-glow: rgba(255,255,255,0.55);
    --motif-fade: rgba(255,255,255,0);
  }
  * { box-sizing: border-box; margin: 0; padding: 0; }
  html, body {
    width: 1200px;
    height: 945px;
    overflow: hidden;
    background: var(--page-bg);
    font-family: "Mulish", sans-serif;
    color: var(--ink);
  }
  .canvas { position: relative; width: 1200px; height: 945px; }
  .panel {
    position: absolute;
    overflow: hidden;
    box-shadow: 0 10px 30px rgba(0,0,0,0.10);
  }
  .bottle-label {
    left: 80px; top: 190px; width: 380px; height: 560px;
    background: linear-gradient(to bottom, var(--teal-light) 0%, var(--teal-light) 22%, var(--teal-mid) 48%, var(--teal-deep) 100%);
    padding: 70px 36px 36px 44px;
  }
  .box-front {
    left: 520px; top: 62px; width: 300px; height: 820px;
    background: linear-gradient(to bottom, var(--teal-light) 0%, var(--teal-light) 18%, var(--teal-mid) 45%, var(--teal-deep) 100%);
    padding: 110px 26px 40px 30px;
  }
  .box-side {
    left: 830px; top: 62px; width: 300px; height: 820px;
    background: linear-gradient(to bottom, var(--side-top) 0%, var(--side-top) 12%, #c9d3d2 40%, var(--side-bottom) 100%);
    padding: 110px 26px 40px 30px;
  }
  .motif {
    position: absolute;
    z-index: 0;
    background: radial-gradient(circle at 50% 50%, var(--motif-glow) 0%, rgba(255,255,255,0.25) 45%, var(--motif-fade) 70%);
  }
  .bottle-label .motif { left: 120px; top: 290px; width: 320px; height: 320px; }
  .box-front .motif { left: -20px; top: 430px; width: 360px; height: 420px; }
  .box-side .motif { left: -140px; top: 430px; width: 360px; height: 420px; }
  .brand, .tagline, .strength, .volume { position: relative; z-index: 1; }
  .brand { display: flex; align-items: center; gap: 10px; }
  .brand-dot {
    width: 14px; height: 14px; border-radius: 50%;
    background: var(--accent); flex: none;
  }
  .brand-name { font-weight: 800; letter-spacing: 0.04em; line-height: 1; color: var(--ink); }
  .tagline { font-weight: 400; letter-spacing: 0.02em; margin-top: 8px; }
  .bottle-label .brand-name { font-size: 46px; }
  .bottle-label .tagline { font-size: 22px; padding-left: 24px; }
  .bottle-label .strength {
    position: absolute; left: 68px; top: 300px;
    font-size: 17px; font-weight: 400;
  }
  .bottle-label .volume { position: absolute; left: 68px; bottom: 44px; font-size: 22px; }
  .box-front .brand-name, .box-side .brand-name { font-size: 40px; }
  .box-front .tagline, .box-side .tagline { font-size: 19px; padding-left: 24px; }
  .box-front .strength {
    position: absolute; left: 54px; top: 400px;
    font-size: 22px; line-height: 1.35; font-weight: 400;
  }
  .box-front .volume { position: absolute; left: 54px; bottom: 40px; font-size: 30px; }
</style>
</head>
<body>
  <main class="canvas">
    <section class="panel bottle-label" aria-label="Bottle label">
      <div class="motif" role="img" aria-label="Large mandala motif in white outline"></div>
      <div class="brand">
        <span class="brand-dot"></span>
        <span class="brand-name">KELVORA</span>
      </div>
      <p class="tagline">Organic Cannabis Oil</p>
      <p class="strength">1500mg (15%) Full Spectrum</p>
      <p class="volume">10ml</p>
    </section>

    <section class="panel box-front" aria-label="Box front panel">
      <div class="motif" role="img" aria-label="Large mandala motif in white outline"></div>
      <div class="brand">
        <span class="brand-dot"></span>
        <span class="brand-name">KELVORA</span>
      </div>
      <p class="tagline">Organic Cannabis Oil</p>
      <p class="strength">1500mg (15%)<br>Full Spectrum</p>
      <p class="volume">10ml</p>
    </section>

    <section class="panel box-side" aria-label="Box side panel">
      <div class="motif" role="img" aria-label="Mandala motif continuing from the front panel"></div>
      <div class="brand">
        <span class="brand-dot"></span>
        <span class="brand-name">KELVORA</span>
      </div>
      <p class="tagline">Organic Cannabis Oil</p>
    </section>
  </main>
</body>
</html>
```